Travel Agency Website - Simple General

Need a 7 page simple design that is pretty repetitive. Need to be able to load quickly that is SEO optimized. Trying to give ideas on what they can do, be personal as we are local, but at the same time come across as professional and get information easily with little burden.

- Landing Page
- Brimwell Vacations Page
- Family Trips
- Road Trips from Texas
- Other Destinations
- About Us Page
- Contact Us Page

Target Market(s)

Families

Coding

Coded - Design and coding required

Number of Pages Required

5+ page

Colors

Designer to choose colors to be used in the design.

Requirements
Must have
• Like it to flow easily with our logo. Use that for colors, etc.

```html
<!DOCTYPE html>
<html lang="en">
<head>
<meta charset="utf-8">
<title>Meadowlark Roaming – Contact</title>
<link href="https://fonts.googleapis.com/css2?family=Outfit:wght@400;500&family=Sofia+Sans+Extra+Condensed:wght@600;700&display=swap" rel="stylesheet">
<style>
:root{
  --bg:#e3e7e1;
  --navy:#0f3f52;
  --teal:#338b8e;
  --gold:#c4964c;
  --white:#ffffff;
  --card-edge:#eef1ec;
}
*{box-sizing:border-box;margin:0;padding:0}
html,body{width:983px;height:1200px;overflow:hidden}
body{position:relative;background:var(--bg);font-family:"Outfit",sans-serif;color:var(--navy)}
.cond{font-family:"Sofia Sans Extra Condensed",sans-serif}
.brand{position:absolute;left:103px;top:26px;width:80px;text-align:center;display:flex;flex-direction:column;align-items:center;gap:4px}
.brand-dot{width:14px;height:14px;border-radius:50%;background:var(--teal)}
.brand-name{font-size:13px;font-weight:500;color:var(--navy);line-height:1.1}
.nav{position:absolute;top:42px;left:422px;display:flex;gap:20px;font-size:8.6px;list-style:none}
.page-title{position:absolute;top:132px;left:0;width:983px;text-align:center;font-size:46px;font-weight:700;letter-spacing:-.2px}
.backdrop{position:absolute;left:0;top:500px;width:983px;height:620px;
  background:radial-gradient(ellipse at 75% 55%,rgba(170,140,110,.35),transparent 55%),linear-gradient(180deg,rgba(200,210,205,.2),rgba(190,205,210,.45) 50%,rgba(227,231,225,0))}
.gallery{position:absolute;top:212px;left:0;width:983px;height:290px}
.card{position:absolute;top:0;width:246px;height:287px;border-radius:16px;background:var(--card-edge);padding:4px;box-shadow:0 4px 14px rgba(0,0,0,.06)}
.card-photo{width:100%;height:100%;border-radius:13px;position:relative;overflow:hidden}
.card-photo::after{content:"";position:absolute;inset:0;background:linear-gradient(180deg,transparent 55%,rgba(232,235,230,.95) 85%)}
.card-label{position:absolute;left:0;right:0;top:226px;text-align:center;font-size:21px;font-weight:700;z-index:1}
.beach{background:linear-gradient(180deg,#4f7a70 0%,#5f8275 45%,#7a6550 75%)}
.mountain{background:linear-gradient(180deg,#4d6a3a,#6f9446 50%,#8aa95c)}
.road{background:linear-gradient(180deg,#b8b4a6,#6a7a4e 40%,#4a4c4e 75%)}
.city{background:linear-gradient(180deg,#a8cfe0,#7e9a7a 55%,#9aa5a8)}
.form-panel{position:absolute;left:296px;top:596px;width:390px;height:428px;border-radius:28px;background:var(--teal);opacity:.97}
.form-title{position:absolute;top:32px;left:0;width:100%;text-align:center;color:var(--white);font-size:25px;font-weight:700}
.field-label{position:absolute;color:var(--white);font-size:10.5px;font-weight:600}
.field{position:absolute;background:var(--white);border-radius:4px;height:29px}
.notes{height:82px}
.submit{position:absolute;left:47px;top:358px;width:297px;height:29px;border-radius:4px;background:var(--gold);color:var(--white);font-size:10.5px;font-weight:600;display:flex;align-items:center;justify-content:center}
.contact{position:absolute;top:1107px;display:flex;align-items:center;gap:9px}
.icon-circle{width:40px;height:40px;border-radius:50%;background:var(--gold);display:flex;align-items:center;justify-content:center}
.contact-kicker{font-size:8.5px;font-weight:500}
.contact-value{font-size:11px}
.social{position:absolute;top:1115px;display:flex;align-items:center;gap:6px;font-size:9px}
.social-dot{width:22px;height:22px;border-radius:50%;background:var(--gold)}
.social a{color:var(--navy);text-decoration:underline}
</style>
</head>
<body>
<header>
  <div class="brand"><span class="brand-dot"></span><span class="brand-name">Meadowlark Roaming</span></div>
  <ul class="nav">
    <li>Home</li><li>Brimwell Vacations</li><li>Family Trips</li><li>Texas Road Trips</li><li>Other Destinations</li><li>About Us</li><li>Contact</li>
  </ul>
</header>

<h1 class="page-title cond">Pictures of Trips Our Family Took</h1>

<div class="backdrop" role="img" aria-label="Faded photo of a traveller in a straw hat looking through binoculars by the water"></div>

<section class="gallery">
  <div class="card" style="left:-16px"><div class="card-photo beach" role="img" aria-label="Beach chairs and umbrella by the sea"></div><p class="card-label cond">Beach Trip</p></div>
  <div class="card" style="left:240px"><div class="card-photo mountain" role="img" aria-label="Hikers walking a green mountain valley"></div><p class="card-label cond">Mountain Trip</p></div>
  <div class="card" style="left:496px"><div class="card-photo road" role="img" aria-label="Car driving a winding mountain road"></div><p class="card-label cond">Road Trip</p></div>
  <div class="card" style="left:752px"><div class="card-photo city" role="img" aria-label="City skyline with tall towers and trees"></div><p class="card-label cond">City Trip</p></div>
</section>

<form class="form-panel">
  <h2 class="form-title cond">Plan Your Family Trip</h2>
  <span class="field-label cond" style="left:46px;top:82px">Which Trip Are You Interested In?</span>
  <span class="field-label cond" style="left:198px;top:82px">How Many People in Your Party?</span>
  <span class="field" style="left:47px;top:100px;width:145px"></span>
  <span class="field" style="left:199px;top:100px;width:145px"></span>
  <span class="field-label cond" style="left:46px;top:136px">Start Date</span>
  <span class="field-label cond" style="left:198px;top:136px">End Date</span>
  <span class="field" style="left:47px;top:155px;width:145px"></span>
  <span class="field" style="left:199px;top:155px;width:145px"></span>
  <span class="field-label cond" style="left:46px;top:193px">What Kind of Trip Are You Looking For?</span>
  <span class="field" style="left:47px;top:212px;width:297px"></span>
  <span class="field-label cond" style="left:46px;top:249px">Any Additional Notes</span>
  <span class="field notes" style="left:47px;top:268px;width:297px"></span>
  <span class="submit cond">SUBMIT REQUEST</span>
</form>

<footer>
  <div class="contact" style="left:196px">
    <span class="icon-circle"><svg width="14" height="14" viewBox="0 0 24 24"><path fill="#fff" d="M6.6 10.8a15 15 0 006.6 6.6l2.2-2.2c.3-.3.7-.4 1-.2 1.1.4 2.3.6 3.6.6.6 0 1 .4 1 1V20c0 .6-.4 1-1 1A17 17 0 013 4c0-.6.4-1 1-1h3.5c.6 0 1 .4 1 1 0 1.3.2 2.5.6 3.6.1.3 0 .7-.2 1z"/></svg></span>
    <div><p class="contact-kicker">Call Us:</p><p class="contact-value">111.111.1111</p></div>
  </div>
  <div class="contact" style="left:342px">
    <span class="icon-circle"><svg width="14" height="11" viewBox="0 0 24 18"><path fill="#fff" d="M0 2l12 8 12-8V0H0zM0 4.5V18h24V4.5l-12 8z"/></svg></span>
    <div><p class="contact-kicker">Email Address:</p><p class="contact-value">HelloMeadowlarkRoaming@mailbox.com</p></div>
  </div>
  <div class="social" style="left:622px"><span class="social-dot"></span><a>Friendpage</a></div>
  <div class="social" style="left:720px"><span class="social-dot"></span><a>Snapshelf</a></div>
</footer>
</body>
</html>
```